Veldmark Supplies Business Card

Professional business card that stand out to our potential customers. Front and back with clean modern design

Industry/Entity Type

Oil and gas

Contact Information for Business Card

Name, address, website , office phone and cell number

Requirements
Must have
• Editable files for each employee

```html
<!DOCTYPE html>
<html lang="en">
<head>
<meta charset="UTF-8">
<title>Veldmark Supplies Business Card</title>
<link href="https://fonts.googleapis.com/css2?family=Poppins:wght@300;400;700&display=swap" rel="stylesheet">
<style>
  :root {
    --brand-red: #ea2627;
    --brand-blue: #12b0d3;
    --ink: #111111;
    --paper: #ffffff;
    --backdrop: #e3e7e9;
  }
  * { margin: 0; padding: 0; box-sizing: border-box; }
  html, body {
    width: 1200px;
    height: 960px;
    overflow: hidden;
    background: var(--backdrop);
    font-family: "Poppins", sans-serif;
  }
  .card {
    position: absolute;
    left: 250px;
    width: 701px;
    height: 400px;
    background: var(--paper);
    overflow: hidden;
  }
  .card--front { top: 60px; }
  .card--back { top: 500px; }

  /* Front */
  .front-brand {
    position: absolute;
    inset: 0;
    display: flex;
    align-items: center;
    justify-content: center;
    gap: 16px;
  }
  .brand-square {
    width: 34px;
    height: 34px;
    background: var(--brand-red);
  }
  .brand-name {
    font-weight: 700;
    color: var(--brand-red);
    letter-spacing: 0.5px;
    white-space: nowrap;
  }
  .front-brand .brand-name { font-size: 40px; }

  /* Back */
  .back-brand {
    position: absolute;
    left: 28px;
    top: 26px;
  }
  .back-brand .brand-name { font-size: 30px; line-height: 40px; }

  .accent-bar {
    position: absolute;
    left: 0;
    top: 135px;
    width: 18px;
    height: 53px;
    background: var(--brand-red);
  }
  .person {
    position: absolute;
    left: 24px;
    top: 124px;
  }
  .person-name {
    font-size: 35px;
    line-height: 40px;
    white-space: nowrap;
  }
  .person-name .given { font-weight: 700; color: var(--brand-red); }
  .person-name .family { font-weight: 300; color: var(--brand-blue); }
  .person-title {
    font-size: 18px;
    line-height: 24px;
    color: var(--ink);
    margin-top: 2px;
  }

  .contact-band {
    position: absolute;
    left: 0;
    right: 0;
    top: 200px;
    bottom: 0;
    background: var(--brand-blue);
    color: var(--paper);
  }
  .address {
    position: absolute;
    left: 24px;
    top: 10px;
    font-size: 17.5px;
    line-height: 23px;
    letter-spacing: 0.3px;
  }
  .contact-list {
    position: absolute;
    left: 24px;
    top: 82px;
    list-style: none;
  }
  .contact-list li {
    display: flex;
    align-items: center;
    gap: 14px;
    height: 22px;
    font-size: 17.5px;
    letter-spacing: 0.3px;
  }
  .contact-icon {
    width: 16px;
    height: 16px;
    flex: none;
  }
</style>
</head>
<body>

<section class="card card--front">
  <div class="front-brand">
    <span class="brand-square"></span>
    <span class="brand-name">Veldmark Supplies</span>
  </div>
</section>

<section class="card card--back">
  <div class="back-brand">
    <span class="brand-name">Veldmark Supplies</span>
  </div>

  <span class="accent-bar"></span>
  <div class="person">
    <p class="person-name"><span class="given">Marika</span> <span class="family">Dellweg</span></p>
    <p class="person-title">Co-Founder &amp; CEO</p>
  </div>

  <div class="contact-band">
    <p class="address">408 Quarrystone Lane,<br>Brookhollow, TX 79412</p>
    <ul class="contact-list">
      <li>
        <svg class="contact-icon" viewBox="0 0 16 16" aria-hidden="true">
          <path d="M3 1.5 L5.5 1 L7 4.5 L5.3 5.8 C6 7.6 8.2 9.9 10.2 10.7 L11.5 9 L15 10.5 L14.5 13 C13.8 14.5 11.5 15 9 13.8 C5.5 12 3 9 1.8 6 C1 4 1.5 2.3 3 1.5 Z" fill="none" stroke="currentColor" stroke-width="1.3" stroke-linejoin="round"/>
        </svg>
        <span>(806) 412-5730</span>
      </li>
      <li>
        <svg class="contact-icon" viewBox="0 0 16 16" aria-hidden="true">
          <rect x="4" y="0.8" width="8" height="14.4" rx="1.2" fill="none" stroke="currentColor" stroke-width="1.4"/>
          <line x1="6.8" y1="12.8" x2="9.2" y2="12.8" stroke="currentColor" stroke-width="1.2"/>
        </svg>
        <span>(806) 418-2291</span>
      </li>
      <li>
        <svg class="contact-icon" viewBox="0 0 16 16" aria-hidden="true">
          <circle cx="8" cy="8" r="7" fill="none" stroke="currentColor" stroke-width="1.3"/>
          <ellipse cx="8" cy="8" rx="3" ry="7" fill="none" stroke="currentColor" stroke-width="1.1"/>
          <line x1="1" y1="8" x2="15" y2="8" stroke="currentColor" stroke-width="1.1"/>
        </svg>
        <span>www.veldmarksupplies.com</span>
      </li>
      <li>
        <svg class="contact-icon" viewBox="0 0 16 16" aria-hidden="true">
          <rect x="1" y="5" width="14" height="10" fill="none" stroke="currentColor" stroke-width="1.3"/>
          <path d="M1 5 L8 10.5 L15 5" fill="none" stroke="currentColor" stroke-width="1.2"/>
          <path d="M4 6 V2 H12 V6" fill="none" stroke="currentColor" stroke-width="1.1"/>
        </svg>
        <span>info@veldmarksupplies.com</span>
      </li>
    </ul>
  </div>
</section>

</body>
</html>
```